Telecommunications/Power civil contractor needs business card design

Were a new telecommunications/power underground civil contractor that is looking for a new business card design. Our company colours are silver or grey and orange. Feel free to use the white background logo or the black background logo.

Target Market(s)

Local contractors, utility companies, private sector mining/energy companies, developers.

Industry/Entity Type

Telecommunications

Contact Information for Business Card

Each card will need the following info:
Persons name:
Title:
E-mail:
Phone number:
Shop Address:
Mailing Address:

Requirements
Must have
• Each card will need the following info:
• Persons name:
• Title:
• E-mail:
• Phone number:
• Shop Address:
• Mailing Address:

```html
<!DOCTYPE html>
<html lang="en">
<head>
<meta charset="utf-8">
<title>Ridgeline Contracting Inc – Business Card</title>
<link rel="stylesheet" href="https://fonts.googleapis.com/css2?family=Arimo:wght@400;700&display=swap">
<style>
  :root {
    --page-bg: #4a413b;
    --card-black: #1b1b1c;
    --card-edge: #0f0f10;
    --orange: #f15a24;
    --grey: #9a9a9c;
    --white: #f2f2f2;
    --emboss: #3a3a3c;
  }
  * { box-sizing: border-box; margin: 0; padding: 0; }
  html, body {
    width: 1200px; height: 787px; overflow: hidden;
    background: var(--page-bg);
    font-family: "Arimo", Arial, sans-serif;
  }
  .stage { position: relative; width: 1200px; height: 787px; }
  .card {
    position: absolute;
    width: 525px; height: 300px;
    background: var(--card-black);
    border-radius: 4px;
    box-shadow: 0 10px 24px rgba(0,0,0,.35);
  }
  .card--back { left: 50px; top: 244px; }
  .card--front { left: 625px; top: 244px; }

  /* back side */
  .back-mark {
    position: absolute; inset: 0;
    display: flex; flex-direction: column; align-items: center; justify-content: center; gap: 18px;
  }
  .back-mark__circle {
    width: 120px; height: 120px; border-radius: 50%;
    border: 6px solid var(--emboss);
  }
  .back-mark__name {
    font-weight: 700; font-size: 22px; letter-spacing: 2px; color: var(--emboss);
  }

  /* front side */
  .brand {
    position: absolute; left: 34px; top: 70px; width: 210px;
    display: flex; flex-direction: column; align-items: center;
  }
  .brand__circle {
    width: 80px; height: 80px; border-radius: 50%;
    border: 5px solid var(--orange);
    margin-bottom: 14px;
  }
  .brand__name {
    font-weight: 700; color: var(--orange); text-align: center;
    font-size: 26px; line-height: 1.05; letter-spacing: 1px;
  }
  .brand__name small { display: block; font-size: 13px; letter-spacing: 1.6px; margin-top: 4px; }

  .divider {
    position: absolute; left: 262px; top: 50px; width: 1px; height: 200px;
    background: linear-gradient(to bottom, rgba(255,255,255,0), rgba(255,255,255,.75), rgba(255,255,255,0));
  }

  .contact {
    position: absolute; left: 284px; top: 56px; color: var(--white);
    font-size: 15px; line-height: 1.3;
  }
  .contact__name { color: var(--orange); font-size: 19px; font-weight: 400; }
  .contact__title { margin-bottom: 10px; }
  .contact__address { margin-bottom: 10px; }
  .contact__list { list-style: none; }
  .contact__list li { display: flex; align-items: center; gap: 10px; margin-bottom: 3px; }
  .contact__icon { width: 13px; height: 13px; fill: var(--orange); flex: none; }
</style>
</head>
<body>
<main class="stage">
  <section class="card card--back" aria-label="Card back">
    <div class="back-mark">
      <div class="back-mark__circle"></div>
      <div class="back-mark__name">RIDGELINE CONTRACTING INC</div>
    </div>
  </section>

  <section class="card card--front" aria-label="Card front">
    <div class="brand">
      <div class="brand__circle"></div>
      <div class="brand__name">RIDGELINE<small>CONTRACTING INC</small></div>
    </div>

    <div class="divider"></div>

    <div class="contact">
      <p class="contact__name">Mark Ellison</p>
      <p class="contact__title">President</p>
      <p class="contact__address">2140 Harlow Avenue<br>Millbrook, NY 12545</p>
      <ul class="contact__list">
        <li>
          <svg class="contact__icon" viewBox="0 0 24 24" aria-hidden="true"><path d="M6.6 10.8a15.1 15.1 0 0 0 6.6 6.6l2.2-2.2c.3-.3.7-.4 1-.2 1.1.4 2.3.6 3.6.6.6 0 1 .4 1 1V20c0 .6-.4 1-1 1A17 17 0 0 1 3 4c0-.6.4-1 1-1h3.5c.6 0 1 .4 1 1 0 1.3.2 2.5.6 3.6.1.3 0 .7-.2 1z"/></svg>
          <span>555 0142 7781</span>
        </li>
        <li>
          <svg class="contact__icon" viewBox="0 0 24 24" aria-hidden="true"><path d="M2 5h20v14H2z M2 5l10 8 10-8" stroke="#1b1b1c" stroke-width="1.5"/></svg>
          <span>mark@ridgelinecivil.com</span>
        </li>
        <li>
          <svg class="contact__icon" viewBox="0 0 24 24" aria-hidden="true"><circle cx="12" cy="12" r="10"/><path d="M2 12h20M12 2c3 3 3 17 0 20M12 2c-3 3-3 17 0 20" stroke="#1b1b1c" stroke-width="1.5" fill="none"/></svg>
          <span>www.ridgelinecivil.com</span>
        </li>
      </ul>
    </div>
  </section>
</main>
</body>
</html>
```